Meadow Paw Web Site

We have basically a start up business that I need help with. This project is just for the web site.

Our product is a frozen raw pet food that promotes weight control, less shedding, smaller stools and an overall better health. The product is in nugget form similar to what you would see in a steak shish kabob. I only share that with you in case you want to incorporate that in the design.

We have been in business for 17 years but all of our sales have been word of mouth. We are going to be launching an infomercial this summer and I need everything stated previously to be completed before we can launch the infomercial.

We need the following (6) pages:

Home:
This is where we need to have the ability to purchase our products. Our main goal is to get the consumer to purchase our product. We have our own shopping cart so we just need to allow for the insertion of that shopping cart.

Why Raw:
This will just be a page with 4-5 paragraphs and an embedded YouTube video.

How to Use:
We will need a page with a chart (4 Columns wide with 6 rows) as well as an embedded YouTube video.

Customer Success Stories:
Allow us to add these as we move forward. I need a placeholder for an image of the customers pet and a paragraph or two explaining the situation

Where to Buy:
- Online - Find a Retailer - Find a Local Distributor - Call to Order

Contact Us:
Copper Ridge Holdings, Inc.
2740 Copper Rd
Eagan, MN 55148
(800) xxx-xxxx

We need to provide links to our to be created... Facebook page, Twitter Account, Youtube Channel, Google circle, Blog
Updates

All, I have received many front page designs that look good.  Please notice in the brief that I need multiple pages built not just the home page.  

Thanks,

Dale

Reason: I need to see the rest of the pages. Thanks, Dale

Target Market(s)

Women between the ages of 30 & 60.

Industry/Entity Type

Shopping

```html
<!DOCTYPE html>
<html lang="en">
<head>
<meta charset="utf-8">
<title>Meadow Paw – 100% Natural Raw Dog Food</title>
<link href="https://fonts.googleapis.com/css2?family=Open+Sans:ital,wght@0,400;0,600;1,400;1,600&display=swap" rel="stylesheet">
<style>
  :root {
    --rust: #bb3f04;
    --rust-dark: #a83703;
    --amber: #f5a300;
    --amber-deep: #e98a00;
    --ink: #222;
    --body: #555;
    --panel: #f5f5f5;
    --hero-frame: #c8c8c8;
    --footer: #343434;
    --footer-text: #bdbdbd;
  }
  * { box-sizing: border-box; margin: 0; padding: 0; }
  html, body { width: 834px; height: 1200px; overflow: hidden; }
  body { position: relative; background: #fff; font-family: "Open Sans", Arial, sans-serif; color: var(--ink); }
  .abs { position: absolute; }

  .top-bar { left: 0; top: 0; width: 834px; height: 30px; background: var(--rust); }
  .account-links { right: 84px; top: 8px; font-size: 9.5px; color: var(--amber); display: flex; gap: 6px; align-items: center; }
  .account-links .sep { color: var(--amber); }
  .account-links .cart-count { color: #fff; font-weight: 600; }

  .brand { left: 90px; top: 34px; width: 144px; height: 84px; display: flex; align-items: center; gap: 8px; }
  .brand .mark { width: 22px; height: 22px; background: var(--amber-deep); }
  .brand .name { font-size: 20px; font-weight: 600; color: var(--rust); }

  .search { left: 564px; top: 51px; width: 179px; height: 24px; border: 1px solid #d6d6d6; background: #fff; }
  .search span { position: absolute; left: 9px; top: 5px; font-size: 9.5px; font-style: italic; color: #999; }
  .search .go { position: absolute; right: -1px; top: -1px; width: 25px; height: 24px; background: #3a3a3a; }

  .main-nav { left: 267px; top: 92px; display: flex; align-items: center; font-size: 11.2px; color: var(--ink); }
  .main-nav a { color: inherit; text-decoration: none; margin-right: 24px; }
  .main-nav a.active { background: linear-gradient(#f49a10, var(--amber-deep)); color: #fff; width: 63px; height: 26px; display: flex; align-items: center; justify-content: center; margin-right: 12px; }
  .main-nav a:last-child { margin-right: 0; }

  .hero { left: 90px; top: 125px; width: 653px; height: 301px; border: 3px solid var(--hero-frame); background: #161616; overflow: hidden; }
  .hero-photo { position: absolute; right: 0; top: 0; width: 360px; height: 295px; background: radial-gradient(ellipse at 55% 45%, #6a4a33 0%, #3a2a20 40%, #1a1a1a 75%); }
  .hero h1 { position: absolute; left: 30px; top: 55px; font-size: 28.5px; font-weight: 400; line-height: 32px; color: var(--amber); }
  .hero h1 em { font-style: normal; color: #e06a10; }
  .hero p { position: absolute; left: 30px; top: 127px; width: 290px; font-size: 11px; line-height: 14.5px; color: #fff; }
  .hero .btn { left: 30px; top: 187px; width: 94px; height: 30px; font-size: 11px; }
  .dots { position: absolute; left: 30px; top: 268px; display: flex; gap: 5px; }
  .dots i { width: 7px; height: 7px; border-radius: 50%; background: #fff; }
  .dots i:first-child { background: #e05a10; }

  .btn { position: absolute; display: flex; align-items: center; justify-content: center; background: var(--amber); color: var(--rust); font-weight: 600; }

  .info-card { top: 451px; width: 208px; height: 199px; background: var(--panel); }
  .info-card h2 { position: absolute; left: 15px; top: 12px; font-size: 16.5px; font-weight: 400; color: var(--rust); }
  .info-card p { position: absolute; left: 15px; top: 40px; width: 182px; font-size: 9.6px; line-height: 16px; color: var(--body); }
  .info-card .btn { left: 15px; top: 163px; width: 78px; height: 24px; font-size: 9.6px; font-weight: 400; }

  .featured { left: 0; top: 669px; width: 834px; height: 261px; background: var(--rust); }
  .featured h2 { position: absolute; left: 90px; top: 33px; font-size: 16px; font-weight: 400; color: #fff; }
  .food { position: absolute; top: 64px; width: 153px; }
  .food .photo { width: 153px; height: 97px; background: radial-gradient(circle at 50% 50%, #a8323a 0%, #d08a8c 30%, #fff 62%); }
  .food h3 { margin-top: 13px; font-size: 11px; font-weight: 600; color: #fff; }
  .food p { margin-top: 2px; font-size: 9.5px; line-height: 13px; color: #fff; }
  .food .btn { position: absolute; top: 157px; left: 0; width: 62px; height: 26px; font-size: 11px; background: linear-gradient(#f6a51a, var(--amber-deep)); color: #fff; border: 1px solid #fff3; }

  .stories { left: 90px; top: 951px; width: 432px; height: 128px; background: var(--panel); }
  .stories h2, .newsletter h2 { position: absolute; top: 12px; font-size: 16.5px; font-weight: 400; color: var(--rust); }
  .stories h2 { left: 18px; }
  .stories .portrait { position: absolute; left: 19px; top: 50px; width: 62px; height: 62px; border: 1px solid #999; background: linear-gradient(#d9c1a6, #a77e5c); }
  .stories blockquote { position: absolute; left: 96px; top: 46px; width: 325px; font-size: 9.5px; line-height: 16px; font-style: italic; color: var(--body); }
  .stories .q { color: var(--amber); font-size: 20px; font-weight: 600; font-style: normal; line-height: 0; vertical-align: -6px; }
  .stories cite { position: absolute; left: 96px; top: 100px; font-size: 9.5px; font-weight: 600; color: var(--rust); }

  .newsletter { left: 534px; top: 951px; width: 209px; height: 128px; background: var(--panel); }
  .newsletter h2 { left: 16px; }
  .newsletter .field { position: absolute; left: 17px; top: 47px; width: 175px; height: 29px; border: 1px solid #ccc; background: #fff; font-size: 9px; font-style: italic; color: #999; padding: 9px 10px; }
  .newsletter .btn { left: 116px; top: 91px; width: 76px; height: 26px; font-size: 11px; background: linear-gradient(#f49a10, var(--amber-deep)); color: #fff; }

  .site-footer { left: 0; top: 1098px; width: 834px; height: 102px; background: var(--footer); }
  .footer-nav { position: absolute; left: 91px; top: 20px; font-size: 9.5px; color: #ddd; display: flex; gap: 6px; }
  .footer-nav .sep { color: #999; }
  .legal { position: absolute; left: 91px; top: 55px; font-size: 8.5px; line-height: 14px; color: var(--footer-text); }
  .legal .brand-link { color: var(--amber); }
  .connect { position: absolute; left: 664px; top: 20px; font-size: 9.5px; font-weight: 600; color: #fff; }
  .social { position: absolute; left: 665px; top: 43px; display: flex; gap: 6px; }
  .social i { width: 11px; height: 11px; background: #5a7fbf; }
  .social i:nth-child(2) { background: #3ba5d9; }
  .social i:nth-child(3) { background: #c9c9c9; }
  .social i:nth-child(4) { background: #f08a1c; }
  .social i:nth-child(5) { background: #d12a2a; }
</style>
</head>
<body>
  <div class="abs top-bar"></div>
  <div class="abs account-links">
    <span>Log in</span><span class="sep">|</span><span>Register</span><span class="sep">|</span><span>My Account</span><span class="sep">|</span>
    <svg width="14" height="11" viewBox="0 0 14 11"><path d="M1 3h12l-2 7H3z" fill="#fff"/><path d="M4 3l3-2 3 2" stroke="#fff" fill="none"/></svg>
    <span>My Cart $ 0.00 ( <span class="cart-count">item 0</span>)</span>
  </div>

  <div class="abs brand"><span class="mark"></span><span class="name">Meadow Paw</span></div>

  <div class="abs search"><span>Search keywords...</span>
    <div class="go"><svg width="25" height="24" viewBox="0 0 25 24"><circle cx="11" cy="10" r="4.5" stroke="#fff" stroke-width="2" fill="none"/><path d="M14 13l5 5" stroke="#fff" stroke-width="2.5"/></svg></div>
  </div>

  <nav class="abs main-nav">
    <a class="active">Home</a><a>Why RAW</a><a>How to Use</a><a>Success Stories</a><a>Where to Buy</a><a>Contact us</a>
  </nav>

  <section class="abs hero">
    <div class="hero-photo" role="img" aria-label="Spaniel sitting at a table before a plate of raw meat"></div>
    <h1>We Are <em>Dog RAW Food</em><br>Creator and Seller.</h1>
    <p>Sed accumsan sollicitudin sapien, sit amet adipiscing turpis gravida ac. In congue, neque ac lobortis volutpat, libero mauris varius...</p>
    <a class="btn">More Details</a>
    <div class="dots"><i></i><i></i><i></i><i></i></div>
  </section>

  <article class="abs info-card" style="left:90px">
    <h2>Why RAW</h2>
    <p>Aliquam molestie, mi et imperdiet euismod, dui purus auctor tellus, et interdum lacus lectus et ante. Sed accumsan sollicitudin sapien, sit amet adipiscing turpis gravida ac. In congue, neque ac lobortis volutpat, libero mauris varius...</p>
    <a class="btn">Read More</a>
  </article>
  <article class="abs info-card" style="left:313px">
    <h2>How to Use</h2>
    <p>Aliquam molestie, mi et imperdiet euismod, dui purus auctor tellus, et interdum lacus lectus et ante. Sed accumsan sollicitudin sapien, sit amet adipiscing turpis gravida ac. In congue, neque ac lobortis volutpat, libero mauris varius...</p>
    <a class="btn">Read More</a>
  </article>
  <article class="abs info-card" style="left:534px">
    <h2>Where to Buy</h2>
    <p>Aliquam molestie, mi et imperdiet euismod, dui purus auctor tellus, et interdum lacus lectus et ante. Sed accumsan sollicitudin sapien, sit amet adipiscing turpis gravida ac. In congue, neque ac lobortis volutpat, libero mauris varius...</p>
    <a class="btn">Read More</a>
  </article>

  <section class="abs featured">
    <h2>Featured RAW Food</h2>
    <div class="food" style="left:90px"><div class="photo" role="img" aria-label="Bag of frozen raw nuggets"></div><h3>Food Name</h3><p>Lorem ipsum dolor sit amet elit a suscipit sit amet..</p><a class="btn">Details</a></div>
    <div class="food" style="left:257px"><div class="photo" role="img" aria-label="Cut of raw beef"></div><h3>Food Name</h3><p>Lorem ipsum dolor sit amet elit a suscipit sit amet..</p><a class="btn">Details</a></div>
    <div class="food" style="left:424px"><div class="photo" role="img" aria-label="Bag of frozen raw chunks"></div><h3>Food Name</h3><p>Lorem ipsum dolor sit amet elit a suscipit sit amet..</p><a class="btn">Details</a></div>
    <div class="food" style="left:590px"><div class="photo" role="img" aria-label="Piece of raw red meat"></div><h3>Food Name</h3><p>Lorem ipsum dolor sit amet elit a suscipit sit amet..</p><a class="btn">Details</a></div>
  </section>

  <section class="abs stories">
    <h2>Success Stories</h2>
    <div class="portrait" role="img" aria-label="Portrait of a happy customer"></div>
    <blockquote><span class="q">“</span> Vestibulum dolor nulla, ultrices ac tincidunt sed, laoreet non est. Suspendisse lobortis turpis in odio blandit ac interdum lorem euismod. Etiam risus massa, vulputate eu pellentesque et, consectetur a neque... <span class="q">”</span></blockquote>
    <cite>-Lena Marsh</cite>
  </section>

  <section class="abs newsletter">
    <h2>Newsletter Signup</h2>
    <div class="field">Enter Email Address</div>
    <a class="btn">Subscribe</a>
  </section>

  <footer class="abs site-footer">
    <div class="footer-nav"><span>Home</span><span class="sep">/</span><span>Why RAW</span><span class="sep">/</span><span>How to Use</span><span class="sep">/</span><span>Success Stories</span><span class="sep">/</span><span>Where to Buy</span><span class="sep">/</span><span>Contact us</span></div>
    <div class="legal">Copyright © 2014. <span class="brand-link">Meadow Paw.</span> All Right Reserved<br>Term of Use &nbsp;|&nbsp; Privacy Policy</div>
    <div class="connect">Connect Us:</div>
    <div class="social"><i></i><i></i><i></i><i></i><i></i></div>
  </footer>
</body>
</html>
```